TALMORK

The business want a professional looking business card. We have a scetch we will add but want the extra upgrade, and would like more suggestions for variations of our business cards.

```html
<!DOCTYPE html>
<html lang="en">
<head>
<meta charset="UTF-8">
<title>Talmork Business Cards</title>
<link href="https://fonts.googleapis.com/css2?family=Playfair+Display:wght@600;700&family=Poppins:wght@300;400&display=swap" rel="stylesheet">
<style>
  :root {
    --backdrop: #1d1d1f;
    --card-light: #b07f34;
    --card-mid: #94571f;
    --card-dark: #8a4f1e;
    --gold: #efcb72;
    --gold-soft: rgba(232, 190, 110, 0.22);
  }
  * { margin: 0; padding: 0; box-sizing: border-box; }
  html, body { width: 1200px; height: 900px; overflow: hidden; }
  body { background: var(--backdrop); position: relative; font-family: "Poppins", sans-serif; }

  .card {
    position: absolute;
    width: 620px;
    height: 360px;
    border-radius: 22px;
    overflow: hidden;
    background: linear-gradient(110deg, var(--card-light) 0%, var(--card-mid) 30%, var(--card-dark) 60%, var(--card-light) 100%);
    color: var(--gold);
  }
  .card--front { left: 500px; top: 70px; }
  .card--back { left: 100px; top: 470px; }

  .corner-decoration {
    position: absolute;
    right: -60px;
    bottom: -60px;
    width: 320px;
    height: 320px;
    border-radius: 50%;
    background: radial-gradient(circle, var(--gold-soft) 0%, rgba(232,190,110,0.08) 60%, transparent 72%);
  }

  .brand-mark {
    display: block;
    width: 54px;
    height: 54px;
    border-radius: 50%;
    background: var(--gold);
  }
  .wordmark {
    font-family: "Playfair Display", serif;
    font-weight: 600;
    letter-spacing: 0.18em;
    color: var(--gold);
    line-height: 1;
  }
  .tagline {
    font-family: "Poppins", sans-serif;
    font-weight: 400;
    letter-spacing: 0.32em;
    color: var(--gold);
  }

  .front-lockup {
    position: absolute;
    left: 150px;
    top: 70px;
    display: flex;
    flex-direction: column;
    align-items: center;
    gap: 22px;
  }
  .front-lockup .wordmark { font-size: 54px; }
  .front-lockup .tagline { font-size: 14px; margin-top: -12px; }

  .back-lockup {
    position: absolute;
    left: 40px;
    top: 40px;
    display: flex;
    align-items: center;
    gap: 24px;
  }
  .back-lockup .brand-mark { width: 46px; height: 46px; }
  .back-lockup .wordmark { font-size: 46px; }
  .back-lockup .tagline { font-size: 12px; margin-top: 8px; padding-left: 70px; }

  .contact-block {
    position: absolute;
    left: 40px;
    top: 190px;
  }
  .person-name {
    font-family: "Playfair Display", serif;
    font-weight: 700;
    font-size: 22px;
    margin-bottom: 6px;
  }
  .person-role, .person-full {
    font-weight: 300;
    font-size: 14px;
    line-height: 1.4;
  }
  .contact-list { list-style: none; margin-top: 12px; }
  .contact-list li {
    display: flex;
    align-items: center;
    gap: 10px;
    font-size: 14px;
    font-weight: 300;
    line-height: 1.55;
  }
  .contact-list svg { width: 13px; height: 13px; fill: var(--gold); flex: none; }
</style>
</head>
<body>

  <section class="card card--front">
    <div class="corner-decoration" role="img" aria-label="Faint brand motif decoration"></div>
    <div class="front-lockup">
      <span class="brand-mark"></span>
      <div class="wordmark">TALMORK</div>
      <div class="tagline">SINCE 2026</div>
    </div>
  </section>

  <section class="card card--back">
    <div class="corner-decoration" role="img" aria-label="Faint brand motif decoration"></div>
    <div class="back-lockup-wrap">
      <div class="back-lockup">
        <span class="brand-mark"></span>
        <div>
          <div class="wordmark">TALMORK</div>
          <div class="tagline">SINCE 2026</div>
        </div>
      </div>
    </div>
    <div class="contact-block">
      <div class="person-name">Talmork Haugen</div>
      <div class="person-role">CEO &amp; Founder</div>
      <div class="person-full">Lars Ove Haugen</div>
      <ul class="contact-list">
        <li>
          <svg viewBox="0 0 24 24" aria-hidden="true"><path d="M6.6 10.8a15.1 15.1 0 0 0 6.6 6.6l2.2-2.2a1 1 0 0 1 1-.25 11.4 11.4 0 0 0 3.6.57 1 1 0 0 1 1 1V20a1 1 0 0 1-1 1A17 17 0 0 1 3 4a1 1 0 0 1 1-1h3.5a1 1 0 0 1 1 1c0 1.25.2 2.45.57 3.57a1 1 0 0 1-.25 1z"/></svg>
          004791234567
        </li>
        <li>
          <svg viewBox="0 0 24 24" aria-hidden="true"><path d="M2 5h20v14H2z M2 5l10 8 10-8" fill="none" stroke="currentColor"/><path d="M2 5h20v2l-10 7L2 7z"/><path d="M2 8.5l10 7 10-7V19H2z"/></svg>
          talmork.llc@mailbox.com
        </li>
        <li>
          <svg viewBox="0 0 24 24" aria-hidden="true"><path d="M12 2a10 10 0 1 0 0 20 10 10 0 0 0 0-20zm6.9 9h-3a15 15 0 0 0-1.3-6A8 8 0 0 1 18.9 11zM12 4c.9 1.2 1.8 3.6 1.9 7h-3.8C10.2 7.6 11.1 5.2 12 4zM9.4 5a15 15 0 0 0-1.3 6h-3A8 8 0 0 1 9.4 5zM5.1 13h3a15 15 0 0 0 1.3 6A8 8 0 0 1 5.1 13zM12 20c-.9-1.2-1.8-3.6-1.9-7h3.8c-.1 3.4-1 5.8-1.9 7zm2.6-1a15 15 0 0 0 1.3-6h3a8 8 0 0 1-4.3 6z"/></svg>
          www.talmork.llc
        </li>
      </ul>
    </div>
  </section>

</body>
</html>
```